Keystone Trench Co Business Card*

Looking for a professional, clean and crisp business card

I am in the underground utilities industry and am just looking for a really impressive business card. I would like our card to be white with our symbol crisp and clear with it protruding. I also have a business partner that will require his name and info on the card once the design is set. I would like to have our website info on the card which is;
http://keystonetrenchco.example/

Contact Information for Business Card

Website, contact name, number and email

```html
<!DOCTYPE html>
<html lang="en">
<head>
<meta charset="utf-8">
<title>Keystone Trench Co Business Card</title>
<link href="https://fonts.googleapis.com/css2?family=Montserrat:wght@400;600;700&family=Staatliches&display=swap" rel="stylesheet">
<style>
  :root {
    --stage: #141414;
    --card: #232323;
    --card-deep: #1b1c1e;
    --edge-red: #e0262c;
    --steel: #5a6470;
    --steel-light: #9aa6b4;
    --accent-blue: #3f63b3;
    --white: #ffffff;
  }
  * { box-sizing: border-box; margin: 0; padding: 0; }
  html, body {
    width: 1200px; height: 900px; overflow: hidden;
    background: var(--stage);
    font-family: "Montserrat", sans-serif;
  }
  .stage {
    width: 1200px; height: 900px;
    display: flex; flex-direction: column;
    align-items: center; justify-content: center; gap: 40px;
  }
  .card {
    position: relative;
    width: 660px; height: 377px;
    background: var(--card);
    border-bottom: 3px solid var(--edge-red);
    border-left: 3px solid var(--edge-red);
    overflow: hidden;
  }
  /* front */
  .card-front__pattern {
    position: absolute; inset: 0;
    background:
      repeating-linear-gradient(-28deg, rgba(70,80,95,0.18) 0 34px, transparent 34px 78px),
      linear-gradient(135deg, #26292e, var(--card-deep));
  }
  .card-front__mark {
    position: absolute; inset: 0;
    display: flex; align-items: center; justify-content: center; gap: 16px;
  }
  .brand-dot {
    width: 34px; height: 34px; border-radius: 50%;
    background: #3a3d42;
  }
  .card-front__name {
    font-weight: 700; font-size: 34px; letter-spacing: 2px;
    text-transform: uppercase; color: #4a4e55;
  }
  /* back */
  .card-back__brand {
    position: absolute; left: 64px; top: 0; bottom: 0; width: 200px;
    display: flex; flex-direction: column; align-items: center; justify-content: center; gap: 14px;
  }
  .card-back__brand .brand-dot {
    width: 46px; height: 46px; background: var(--white);
  }
  .card-back__brand-name {
    font-weight: 700; font-size: 20px; line-height: 1.25;
    text-align: center; text-transform: uppercase; color: var(--white);
  }
  .card-back__divider {
    position: absolute; left: 292px; top: 118px;
    width: 2px; height: 142px; background: var(--accent-blue);
  }
  .card-back__details {
    position: absolute; left: 322px; top: 112px;
  }
  .person-name {
    font-family: "Staatliches", sans-serif;
    font-size: 34px; letter-spacing: 2px; color: var(--steel-light);
    margin-bottom: 14px;
  }
  .contact-list { list-style: none; }
  .contact-item {
    display: flex; align-items: center; gap: 10px;
    font-size: 15px; color: var(--white); margin-bottom: 9px;
  }
  .contact-item svg { width: 16px; height: 16px; flex: none; }
  .contact-item__domain { color: var(--accent-blue); }
</style>
</head>
<body>
<main class="stage">
  <section class="card card-front">
    <div class="card-front__pattern" role="img" aria-label="Subtle diagonal pattern of dark pipe sections"></div>
    <div class="card-front__mark">
      <span class="brand-dot"></span>
      <span class="card-front__name">Keystone Trench Co</span>
    </div>
  </section>

  <section class="card card-back">
    <div class="card-back__brand">
      <span class="brand-dot"></span>
      <span class="card-back__brand-name">Keystone<br>Trench Co</span>
    </div>
    <div class="card-back__divider"></div>
    <div class="card-back__details">
      <h1 class="person-name">Dale Marrow</h1>
      <ul class="contact-list">
        <li class="contact-item">
          <svg viewBox="0 0 16 16"><circle cx="8" cy="8" r="7" fill="none" stroke="#3f63b3" stroke-width="1.4"/><path d="M5.5 4.5l1.5 0 .7 1.8-1 .8a5 5 0 0 0 2.2 2.2l.8-1 1.8.7v1.5c-3.5.3-6.3-2.5-6-6z" fill="#3f63b3"/></svg>
          555-014-2281
        </li>
        <li class="contact-item">
          <svg viewBox="0 0 16 16"><rect x="1.5" y="3.5" width="13" height="9" fill="none" stroke="#3f63b3" stroke-width="1.4"/><path d="M1.5 3.5L8 9l6.5-5.5" fill="none" stroke="#3f63b3" stroke-width="1.4"/></svg>
          dale@keystonetrenchco.example
        </li>
        <li class="contact-item">
          <svg viewBox="0 0 16 16"><circle cx="8" cy="8" r="6.5" fill="none" stroke="#3f63b3" stroke-width="1.4"/><ellipse cx="8" cy="8" rx="2.8" ry="6.5" fill="none" stroke="#3f63b3" stroke-width="1.2"/><path d="M1.5 8h13" stroke="#3f63b3" stroke-width="1.2"/></svg>
          <span>www.<span class="contact-item__domain">keystonetrenchco.example</span></span>
        </li>
      </ul>
    </div>
  </section>
</main>
</body>
</html>
```